RUVO WARE LTD

Advertisement to get more schools:
use website https://www.ruvo-ware.co.uk for logos etc.
ICT Service Level Agreements for as little as £2000 per year
Unlimited Remote, phone and email support
Unlimited Call outs included
90% fix time within 30 minutes of ticket submission
Extra support during Scolvar inspections
GDPR service included

Education

```html
<!DOCTYPE html>
<html lang="en">
<head>
<meta charset="UTF-8">
<title>RUVO WARE – ICT SLA Agreements</title>
<link href="https://fonts.googleapis.com/css2?family=Poppins:wght@400;500;600;700;800&display=swap" rel="stylesheet">
<style>
  :root {
    --blue: #1b6fc0;
    --blue-deep: #0f4f95;
    --orange: #f4804a;
    --orange-soft: #f9d9c8;
    --ink: #111111;
    --footer: #0a1623;
    --band: #ebf3fc;
    --white: #ffffff;
  }
  * { margin: 0; padding: 0; box-sizing: border-box; }
  html, body { width: 1200px; height: 2256px; overflow: hidden; background: var(--white); }
  body { font-family: "Poppins", sans-serif; color: var(--ink); position: relative; }
  .abs { position: absolute; }

  .brand { left: 0; width: 1200px; top: 140px; text-align: center; }
  .brand-name { display: inline-flex; align-items: center; gap: 18px; font-size: 70px; font-weight: 700; color: var(--blue); letter-spacing: 2px; line-height: 1; }
  .brand-mark { width: 54px; height: 54px; background: var(--orange); border-radius: 6px; }
  .brand-tagline { margin-top: 18px; font-size: 21px; font-weight: 500; letter-spacing: 2px; color: var(--blue); }

  .hero { left: 0; top: 314px; width: 1200px; height: 549px;
    background: linear-gradient(120deg, #2a6cb8 0%, #1d4f8f 45%, #0f2e5a 100%); }
  .hero-title { left: 0; width: 1200px; top: 420px; text-align: center; color: var(--white); font-weight: 800; font-size: 112px; line-height: 104px; letter-spacing: -2px; }
  .offer-bar { left: 216px; top: 668px; width: 769px; height: 63px; background: var(--orange); color: var(--white);
    font-weight: 700; font-size: 40px; text-align: center; line-height: 63px; letter-spacing: -0.5px; }

  .unlimited-frame { left: 203px; top: 927px; width: 789px; height: 690px; border: 3px solid var(--blue); border-bottom: none; }
  .unlimited-title { left: 0; width: 1200px; top: 890px; text-align: center; }
  .unlimited-title span { background: var(--white); padding: 0 16px; font-size: 46px; font-weight: 700; letter-spacing: 9px; color: var(--blue); }

  .service-label { height: 70px; border: 3px solid var(--orange); border-radius: 0 30px 0 30px; border-left-width: 4px;
    font-size: 38px; font-weight: 600; line-height: 64px; padding-left: 30px; background: var(--white); }

  .perks { left: 0; top: 1600px; width: 1200px; height: 413px; background: var(--band); border-top: 3px solid var(--ink); }
  .perk-tag { height: 56px; background: var(--orange); color: var(--white); font-weight: 700; font-size: 30px; text-align: center; line-height: 56px; border-radius: 0 0 14px 14px; }
  .perk-caption { width: 420px; text-align: center; font-size: 32px; line-height: 41px; font-weight: 400; }
  .gdpr-badge { left: 487px; top: 1712px; width: 224px; text-align: center; color: var(--white); font-weight: 700; font-size: 40px; line-height: 44px; }
  .gdpr-badge small { font-size: 29px; font-weight: 600; }

  .footer { left: 0; top: 2013px; width: 1200px; height: 243px; background: var(--footer); }
  .footer-rule { left: 127px; top: 2090px; width: 5px; height: 66px; background: var(--white); }
  .footer-lead { left: 153px; top: 2080px; font-size: 26px; font-weight: 500; color: var(--white); }
  .footer-url { left: 153px; top: 2116px; font-size: 37px; font-weight: 600; color: var(--white); }
  .follow { left: 852px; top: 2070px; width: 200px; text-align: center; font-size: 26px; font-weight: 500; color: var(--white); }
</style>
</head>
<body>

<header class="brand abs">
  <div class="brand-name"><span class="brand-mark"></span>RUVO WARE</div>
  <div class="brand-tagline">EDUCATION SUPPORT &amp; INSTALLATION</div>
</header>

<div class="hero abs" role="img" aria-label="Photo of a student wearing a virtual reality headset in a school classroom, blue tinted"></div>
<h1 class="hero-title abs">ICT SLA<br>AGREEMENTS</h1>
<div class="offer-bar abs">FOR AS LITTLE A £2000 PER YEAR</div>

<div class="unlimited-frame abs"></div>
<div class="unlimited-title abs"><span>UNLIMITED</span></div>

<svg class="abs" style="left:0;top:0" width="1200" height="1600" aria-hidden="true">
  <g fill="none" stroke="#f9c7ae" stroke-width="3" stroke-dasharray="10 8">
    <path d="M383 1190 V1211 H832 V1192"/>
    <path d="M832 1382 V1439 H383 V1385"/>
  </g>
  <g fill="#f4804a" stroke="#f9d9c8" stroke-width="9">
    <circle cx="383" cy="1095" r="90"/>
    <circle cx="832" cy="1287" r="90"/>
    <circle cx="383" cy="1480" r="90"/>
  </g>
  <g fill="none" stroke="#fff" stroke-width="4" stroke-linecap="round" stroke-linejoin="round">
    <rect x="338" y="1055" width="52" height="36" rx="3"/>
    <path d="M354 1091 v8 h20 v-8"/>
    <rect x="378" y="1100" width="52" height="36" rx="3"/>
    <path d="M394 1136 v8 h20 v-8"/>
    <path d="M398 1062 h22 v20 M414 1076 l6 6 6-6"/>
    <path d="M370 1128 h-22 v-20 M342 1114 l6-6 6 6"/>
    <rect x="795" y="1262" width="74" height="50" rx="4"/>
    <path d="M795 1264 l37 30 37-30"/>
    <path d="M812 1262 v-26 h30 l10 10 v16"/>
    <circle cx="832" cy="1250" r="9"/>
    <rect x="358" y="1435" width="46" height="86" rx="7"/>
    <path d="M375 1510 h12"/>
    <path d="M372 1460 c0 14 8 26 20 30 l6-6 -8-8 -5 4 c-5-3-8-8-9-13 l4-5 -7-9z"/>
    <path d="M414 1460 q8 8 0 18 M422 1452 q14 16 0 34"/>
  </g>
</svg>

<div class="service-label abs" style="left:510px;top:1047px;width:357px">Remote</div>
<div class="service-label abs" style="left:324px;top:1263px;width:354px">Email Support</div>
<div class="service-label abs" style="left:510px;top:1484px;width:357px">Call Outs</div>

<section class="perks abs"></section>

<svg class="abs" style="left:0;top:0" width="1200" height="2013" aria-hidden="true">
  <circle cx="599" cy="1801" r="114" fill="#f4804a" stroke="#f9d9c8" stroke-width="9"/>
  <rect x="191" y="1652" width="192" height="152" fill="#1b6fc0" stroke="#0f4f95" stroke-width="6"/>
  <rect x="799" y="1652" width="192" height="152" fill="#1b6fc0" stroke="#0f4f95" stroke-width="6"/>
  <g fill="none" stroke="#fff" stroke-width="4" stroke-linecap="round" stroke-linejoin="round">
    <rect x="235" y="1680" width="56" height="76" rx="4"/>
    <path d="M250 1676 h26 v10 h-26z"/>
    <path d="M244 1700 l5 5 8-9 M264 1702 h18 M244 1720 l5 5 8-9 M264 1722 h18 M244 1740 l5 5 8-9 M264 1742 h14"/>
    <circle cx="308" cy="1742" r="16"/>
    <path d="M308 1733 v9 h7"/>
    <rect x="318" y="1694" width="40" height="34" rx="4" transform="rotate(-25 338 1711)"/>
    <rect x="845" y="1684" width="88" height="64" rx="4"/>
    <path d="M857 1700 h24 M857 1712 h20"/>
    <path d="M858 1738 v-10 M870 1738 v-16 M882 1738 v-8"/>
    <path d="M890 1712 l12-10 10 8 18-18"/>
    <circle cx="930" cy="1690" r="5"/>
    <circle cx="918" cy="1750" r="20"/>
    <circle cx="918" cy="1750" r="9"/>
  </g>
</svg>

<div class="perk-tag abs" style="left:168px;top:1814px;width:260px">90% FIX TIME</div>
<div class="perk-caption abs" style="left:96px;top:1890px">within 30 minutes<br>of ticket submission</div>

<div class="gdpr-badge abs">GDPR<br>SERVICE<br><small>INCLUDED</small></div>

<div class="perk-tag abs" style="left:738px;top:1814px;width:332px">EXTRA SUPPORT</div>
<div class="perk-caption abs" style="left:696px;top:1890px">during Scolvar<br>inspections</div>

<footer class="footer abs"></footer>
<div class="footer-rule abs"></div>
<div class="footer-lead abs">Please visit our website</div>
<div class="footer-url abs">www.ruvo-ware.co.uk</div>
<div class="follow abs">Follow Us</div>
<svg class="abs" style="left:870px;top:2112px" width="164" height="44" aria-hidden="true">
  <g fill="none" stroke="#fff" stroke-width="2.5">
    <circle cx="29" cy="22" r="19"/>
    <circle cx="82" cy="22" r="19"/>
    <circle cx="135" cy="22" r="19"/>
  </g>
</svg>

</body>
</html>
```